Business Card for Industrial Distributor

We need a business card design for an industrial distributor. We sell machine parts for the manufacturing and oil industry. We would like the cards to look clean and modern but with a touch of industry.

Our colors are blue/white.

Please feel free to visit our website www.korvelpartsco.com

Target Market(s)

mexican manufacturers in the automobile/aerospace industry

Industry/Entity Type

Industrial

Colors
ffffff
0555a3

```html
<!DOCTYPE html>
<html lang="en">
<head>
<meta charset="utf-8">
<title>Korvel Business Card</title>
<link rel="stylesheet" href="https://fonts.googleapis.com/css2?family=Arimo:wght@400;700&display=swap">
<style>
  :root {
    --backdrop: #4a403b;
    --card: #151617;
    --card-edge: #1d1e20;
    --brand-blue: #2d4fd0;
    --brand-blue-deep: #0555a3;
    --white: #ffffff;
    --text-soft: #d9dadc;
    --muted: #8a8b8e;
    --emboss: #2a2b2d;
  }
  * { box-sizing: border-box; margin: 0; padding: 0; }
  html, body { width: 1200px; height: 864px; overflow: hidden; }
  body {
    background: var(--backdrop);
    font-family: "Arimo", Arial, sans-serif;
    position: relative;
  }
  .card {
    position: absolute;
    top: 277px;
    width: 540px;
    height: 310px;
    background: var(--card);
    border: 1px solid var(--card-edge);
    overflow: hidden;
  }
  .card--front { left: 40px; }
  .card--back { left: 620px; }

  /* Front */
  .front-mark {
    position: absolute;
    left: 50%;
    top: 92px;
    transform: translateX(-50%);
    display: flex;
    align-items: center;
    gap: 14px;
  }
  .front-mark__dot {
    width: 44px; height: 44px; border-radius: 50%;
    background: var(--emboss);
  }
  .front-mark__name {
    font-size: 46px; font-weight: 700; color: var(--emboss);
  }
  .front-url {
    position: absolute;
    left: 0; right: 0; top: 226px;
    text-align: center;
    font-size: 13px;
    letter-spacing: 5px;
    color: var(--muted);
  }

  /* Back */
  .brand {
    position: absolute;
    left: 38px; top: 128px;
    display: flex; align-items: center; gap: 10px;
  }
  .brand__dot {
    width: 36px; height: 36px; border-radius: 50%;
    background: var(--brand-blue);
  }
  .brand__name {
    font-size: 42px; font-weight: 700; color: var(--brand-blue);
  }
  .divider {
    position: absolute;
    left: 300px; top: 34px;
    width: 1px; height: 250px;
    background: linear-gradient(to bottom, transparent, #9a9b9e 30%, #9a9b9e 70%, transparent);
  }
  .details {
    position: absolute;
    left: 322px; top: 44px;
    color: var(--text-soft);
  }
  .details__name {
    font-size: 17px; color: var(--brand-blue); letter-spacing: 0.5px;
  }
  .details__title {
    font-size: 15px; color: var(--white); margin-top: 2px;
  }
  .details__address {
    font-size: 12px; line-height: 15px; margin-top: 10px; color: var(--text-soft);
  }
  .contact-list { list-style: none; margin-top: 12px; }
  .contact-list li {
    display: flex; align-items: center; gap: 9px;
    font-size: 14px; line-height: 22px; color: var(--white);
  }
  .contact-list svg { width: 14px; height: 14px; fill: var(--brand-blue); flex: none; }
</style>
</head>
<body>
  <section class="card card--front" aria-label="Card front">
    <div class="front-mark">
      <span class="front-mark__dot"></span>
      <span class="front-mark__name">Korvel</span>
    </div>
    <p class="front-url">www.korvelpartsco.com</p>
  </section>

  <section class="card card--back" aria-label="Card back">
    <div class="brand">
      <span class="brand__dot"></span>
      <span class="brand__name">Korvel</span>
    </div>
    <div class="divider"></div>
    <div class="details">
      <p class="details__name">DANIEL REYES</p>
      <p class="details__title">President</p>
      <p class="details__address">Korvel International Corp.<br>4120 Foundry Line Rd.<br>Laredo.TX 78041</p>
      <ul class="contact-list">
        <li>
          <svg viewBox="0 0 16 16" aria-hidden="true"><path d="M3 1l3 3-2 2c1 2 4 5 6 6l2-2 3 3-2 2C7 15 1 9 1 3z"/></svg>
          (555) 318 - 2270
        </li>
        <li>
          <svg viewBox="0 0 16 16" aria-hidden="true"><rect x="4" y="1" width="8" height="5"/><rect x="1" y="6" width="14" height="6" rx="1"/><rect x="4" y="10" width="8" height="5"/></svg>
          (555) 318 - 2274
        </li>
        <li>
          <svg viewBox="0 0 16 16" aria-hidden="true"><path d="M1 3h14v10H1z M1 3l7 6 7-6" stroke="#151617" stroke-width="1"/></svg>
          sales@korvelpartsco.com
        </li>
        <li>
          <svg viewBox="0 0 16 16" aria-hidden="true"><circle cx="8" cy="8" r="7"/><path d="M1 8h14M8 1c3 3 3 11 0 14M8 1c-3 3-3 11 0 14" stroke="#151617" stroke-width="1" fill="none"/></svg>
          www.korvelpartsco.com
        </li>
      </ul>
    </div>
  </section>
</body>
</html>
```